Website & Logo The full package New Business new design and idea

Word Press

Simple, clean and very professional and approachable if possible

I am looking for a full business concept from logo to colour pallet and everything in between.
Brand new business concept, the successful applicant may continue on as our outsourced point person for all future work.

I will have an animated explainer video going over the four keys to business success Staff, Product & Services, Marketing, Sales and why the need a coach just like a sporting team to stay focused and clear on measurable outcomes.

Just added script (pdf attachment) i will be using for the explainer video at top of site.
Updates

Target Market(s)

Small business owners in Australia

Industry/Entity Type

Business Consultant

Number of Pages Required

1 page

Font styles to use
Sans Serif

Colors

Designer to choose colors to be used in the design.

Requirements
Must have
• Word press using Divi platform
• Ball park as per pdf uploaded
• Must work on all devices
• Social links
• Clear and straight forward movement through site
• Great capture of name and email,
• Free Download
• 10 Things you can start today in your small business to get you going again!
Nice to have
• clean one page potentially
• Free files and resources page
Should not have
• boring old menu and old framing

```html
<!DOCTYPE html>
<html lang="en">
<head>
<meta charset="utf-8">
<title>Harbourline Business Coach</title>
<link href="https://fonts.googleapis.com/css2?family=Montserrat:wght@400;500;600&display=swap" rel="stylesheet">
<style>
:root{
  --mint:#e2f8f1;
  --navy:#1f3763;
  --ink:#2b3f5e;
  --body:#6a6f78;
  --green-a:#9aecb4;
  --green-b:#72e39c;
  --accent:#4fd58a;
  --white:#ffffff;
  --field:#eeeeee;
}
*{box-sizing:border-box;margin:0;padding:0}
html,body{width:1200px;height:5100px;overflow:hidden}
body{position:relative;background:var(--white);font-family:'Montserrat',sans-serif;color:var(--body)}
.backdrop{position:absolute;left:0;top:0;width:1200px;height:5100px;z-index:0}
.abs{position:absolute;z-index:1}
h1,h2,h3{font-family:'Montserrat',sans-serif;color:var(--navy);font-weight:500}
p,li{font-size:13px;line-height:24px}

/* header */
.brand{left:119px;top:28px;display:flex;align-items:center;gap:14px}
.brand-dot{width:44px;height:44px;border-radius:50%;background:var(--accent)}
.brand-name{font-size:23px;line-height:29px;color:var(--navy);font-weight:500}
.nav{left:530px;top:38px;display:flex;gap:25px;list-style:none}
.nav li{font-size:13px;color:var(--navy);font-weight:500}

/* hero */
.hero-kicker{left:122px;top:246px;font-size:29px;color:#556575;font-weight:400}
.hero-title{left:122px;top:296px;font-size:45px;line-height:60px;width:460px}
.hero-lead{left:124px;top:437px;width:400px;font-size:13px;line-height:24px;color:var(--ink)}
.play{left:612px;top:436px;width:56px;height:56px;border-radius:50%;background:var(--white);border:6px solid var(--green-b);display:flex;align-items:center;justify-content:center}

/* packages */
.pkg{background:var(--white);box-shadow:0 6px 18px rgba(0,0,0,.12);padding:36px 28px 0 27px}
.pkg h3{font-size:18px;line-height:26px;margin-bottom:16px}
.pkg p{font-size:12.5px;line-height:24px;color:#7a7f87}
.pkg .more{display:flex;align-items:center;gap:10px;margin-top:18px;font-size:14px;color:var(--navy);font-weight:500}
.pkg .more span{display:block;width:118px;height:1px;background:var(--navy)}
.pkg-free{left:89px;top:691px;width:262px;height:323px;background:linear-gradient(180deg,var(--green-a),var(--green-b))}
.pkg-free h3{color:#1d3a3a}
.pkg-free p{color:#3b6e58}
.pkg-special{left:390px;top:832px;width:258px;height:326px}
.pkg-plus{left:89px;top:1069px;width:262px;height:307px}
.packages-intro{left:766px;top:950px;width:330px}
.packages-intro h2{font-size:29px;margin-bottom:18px}
.packages-intro p{color:#5f6670}

/* about me */
.about-me{left:111px;top:1490px;width:410px}
.about-me h2{font-size:41px;margin-bottom:26px}
.about-me p{font-size:12.5px;line-height:24px;text-align:justify}
.btn{display:inline-flex;align-items:center;justify-content:center;height:52px;border-radius:26px;background:var(--navy);color:var(--white);font-size:15px;font-weight:500}
.btn-outline{background:var(--white);color:var(--navy);border:2px solid var(--navy)}

/* snapshot */
.snapshot-title{left:0;top:2050px;width:1200px;text-align:center;font-size:41px}
.snapshot-date{left:0;top:2130px;width:1200px;text-align:center;font-size:18px;color:#666}
.snapshot-box{left:111px;top:2194px;width:453px;height:222px;background:#f3f3f3;box-shadow:0 6px 16px rgba(0,0,0,.12);padding:36px 30px 0 22px}
.snap-item{display:flex;gap:14px;margin-bottom:18px}
.snap-item p{font-size:12.5px;line-height:24px;text-align:justify}
.ring{flex:none;width:19px;height:19px;margin-top:3px}
.failure{left:634px;top:2198px;width:440px}
.failure h3{font-size:18px;margin-bottom:18px}
.failure ul{list-style:none}
.failure li{display:flex;gap:12px;font-size:12.5px;line-height:22px;margin-bottom:13px}
.failure li b{color:var(--navy);font-weight:600;flex:none}

/* about company */
.company{left:642px;top:2570px;width:412px}
.company h2{font-size:44px;margin-bottom:26px}
.company p{font-size:12.5px;line-height:24px;margin-bottom:10px;text-align:justify}
.company-actions{left:642px;top:3000px;display:flex;gap:20px}

/* how it works */
.works{left:111px;top:3330px;width:400px}
.works h2{font-size:41px;margin-bottom:24px}
.works p{font-size:12.5px;line-height:24px}

/* activates */
.bridge{left:180px;top:3800px;width:840px;text-align:center;font-size:14px;line-height:29px;color:#4e5866}
.activates{left:238px;top:3940px;width:760px}
.activates h2{font-size:41px;margin-bottom:24px}
.activates ul{list-style:none}
.activates li{display:flex;gap:18px;font-size:14px;line-height:26px;color:#4e5866;margin-bottom:12px}
.activates .ring{width:21px;height:21px;margin-top:2px}
.free-link{left:238px;top:4452px;font-size:15px;color:var(--navy);text-decoration:underline}

/* newsletter */
.newsletter{left:111px;top:4588px;width:479px;height:348px;background:var(--white);box-shadow:0 6px 18px rgba(0,0,0,.12);padding:38px 48px 0 48px}
.newsletter h2{font-size:27px;text-align:center;margin-bottom:26px}
.field{height:62px;background:var(--field);border:1px solid #e2e2e2;margin-bottom:10px;padding:0 32px;display:flex;align-items:center;font-size:13px;color:#9aa0a6}
.submit{height:62px;background:var(--navy);color:var(--white);display:flex;align-items:center;justify-content:center;font-size:17px;font-weight:500;margin-top:20px}
.application{left:632px;top:4604px;width:420px}
.application h2{font-size:41px;margin-bottom:20px}
.application p{font-size:12.5px;line-height:24px;margin-bottom:8px}

/* footer */
.footer{left:0;top:4990px;width:1200px;height:110px;background:var(--mint)}
.social{position:absolute;left:530px;top:26px;display:flex;gap:12px}
.social span{width:25px;height:25px;border-radius:50%;border:1.5px solid var(--navy)}
.copyright{position:absolute;left:0;top:74px;width:1200px;text-align:center;font-size:14px;color:#5f6670}
</style>
</head>
<body>

<svg class="backdrop" viewBox="0 0 1200 5100" aria-hidden="true">
  <path fill="var(--mint)" d="M0 0H1200V1130C1120 1010 990 900 860 830C700 740 560 650 440 660C310 672 160 710 0 690Z"/>
  <path fill="var(--mint)" d="M1200 3600V4000C1080 3930 900 3880 700 3940C470 4010 300 4200 170 4380C110 4470 50 4560 0 4620V4060C160 3930 420 3840 700 3760C900 3705 1060 3660 1200 3600Z"/>
</svg>

<!-- header -->
<div class="abs brand"><span class="brand-dot"></span><div class="brand-name">Harbourline<br>Business Coach</div></div>
<ul class="abs nav"><li>Home</li><li>About Me</li><li>Company</li><li>How It Works</li><li>Special Offer</li><li>Contact Us</li></ul>

<!-- hero -->
<div class="abs hero-kicker">Welcome To</div>
<h1 class="abs hero-title">Harbourline Business Coach</h1>
<p class="abs hero-lead">Lorem ipsum dolor sit amet, consectetur adipiscing elit, sed do eiusmod tempor incididunt ut</p>
<svg class="abs" style="left:614px;top:158px" width="476" height="484" viewBox="0 0 476 484" role="img" aria-label="Photo of a business coach speaking in a meeting">
  <defs><linearGradient id="heroPhoto" x1="0" y1="0" x2="1" y2="1"><stop offset="0" stop-color="#8c7a66"/><stop offset=".5" stop-color="#d9d4cc"/><stop offset="1" stop-color="#b79a72"/></linearGradient></defs>
  <path fill="url(#heroPhoto)" d="M60 30C140-10 280 0 380 70C470 135 490 240 430 330C370 420 280 480 200 484C150 486 120 440 80 380C30 300 0 220 10 140C16 90 25 50 60 30Z"/>
</svg>
<div class="abs play"><svg width="12" height="12" viewBox="0 0 12 12"><path d="M2 1L11 6L2 11Z" fill="var(--navy)"/></svg></div>

<!-- packages -->
<div class="abs pkg pkg-free">
  <h3>Giving Back Free</h3>
  <p>Harbourline Business Coach is offering 4 FREE 12-week coaching one on one support program every 3 months to struggling businesses in 2019 as our way of giving back and helping others in need.</p>
  <div class="more">View More <span></span></div>
</div>
<div class="abs pkg pkg-special">
  <h3>Special Offer - Below Cost Price $200 a week for 12 weeks</h3>
  <p>Harbourline Business Coach is offering this incredible one on one support program to only 12 small business owners in the first quarter in 2019</p>
  <div class="more">View More <span></span></div>
</div>
<div class="abs pkg pkg-plus">
  <h3>Just A Bit More $400 a week for 12 weeks</h3>
  <p>Very limited on application only just 4 clients per quarter, here we provide additional one on onesupport each week and dive deeper into every element of your business and fast track</p>
  <div class="more">View More <span></span></div>
</div>
<div class="abs packages-intro">
  <h2>Choose Our Packages</h2>
  <p>Lorem ipsum dolor sit amet, consectetur adipiscing elit, sed do eiusmod tempor incididunt ut labore et dolore magna aliqua.</p>
</div>

<!-- about me -->
<div class="abs about-me">
  <h2>About Me</h2>
  <p>I am not superman, I just found myself absorbing information over the past 10 years through some mentors and personal development and see so many small business owners struggling and I got sick of telling myself how I would change things then I eventually approached some businesses for free and asked if they needed a hand and theywere over the moon, very receptive and after a 1 hour talk the immediate action taken saw some massive returns exceeding even my estimates and now I just want to help more Small Business Owners through Harbourline Business Coach support.</p>
  <div class="btn" style="width:198px;margin-top:30px">Read More</div>
</div>
<svg class="abs" style="left:606px;top:1478px" width="480" height="446" viewBox="0 0 480 446" role="img" aria-label="Photos of coaching sessions with business owners">
  <defs><linearGradient id="aboutPhoto" x1="0" y1="0" x2="1" y2="1"><stop offset="0" stop-color="#6b5a4c"/><stop offset=".55" stop-color="#c9c3bb"/><stop offset="1" stop-color="#8a9aa8"/></linearGradient></defs>
  <path fill="url(#aboutPhoto)" stroke="#fff" stroke-width="4" d="M40 20C100-5 200 0 260 50C300 90 290 170 250 230C210 290 150 300 100 280C40 255 5 200 2 130C0 80 10 35 40 20Z"/>
  <path fill="url(#aboutPhoto)" stroke="#fff" stroke-width="4" d="M370 150C410 130 460 150 475 190C488 230 460 285 420 294C380 300 345 280 340 240C336 200 345 165 370 150Z"/>
  <path fill="url(#aboutPhoto)" stroke="#fff" stroke-width="4" d="M200 290C240 275 300 290 322 340C340 385 310 430 260 442C220 450 190 420 180 380C172 345 175 302 200 290Z"/>
</svg>

<!-- snapshot -->
<h2 class="abs snapshot-title">Australian Small Business Snapshot</h2>
<div class="abs snapshot-date">Nov 26, 2018</div>
<div class="abs snapshot-box">
  <div class="snap-item"><svg class="ring" viewBox="0 0 20 20"><circle cx="10" cy="10" r="8.5" fill="none" stroke="var(--navy)" stroke-width="1.4"/><path d="M8.5 6.5L12 10L8.5 13.5" fill="none" stroke="var(--navy)" stroke-width="1.4"/></svg><p>It's an extremely sad sign of the times when you're confronted with a myriad of 'for lease' signs in shop windows along major shopping hubs.</p></div>
  <div class="snap-item"><svg class="ring" viewBox="0 0 20 20"><circle cx="10" cy="10" r="8.5" fill="none" stroke="var(--navy)" stroke-width="1.4"/><path d="M8.5 6.5L12 10L8.5 13.5" fill="none" stroke="var(--navy)" stroke-width="1.4"/></svg><p>While most businesses in Australia are small -- accounting for 97 percent of all businesses -- they're shutting their doors in alarmingly high numbers.</p></div>
</div>
<div class="abs failure">
  <h3>What is the Small Business Failure Rate?</h3>
  <ul>
    <li><b>&gt;&gt;</b>20% of small businesses fail in their first year</li>
    <li><b>&gt;&gt;</b>30% of small businesses fail in their second year</li>
    <li><b>&gt;&gt;</b>50% of small businesses fail after five years in business.</li>
    <li><b>&gt;&gt;</b>Finally, 70% of small business owners fail in their 10th year in business.</li>
  </ul>
</div>

<!-- about company -->
<svg class="abs" style="left:0;top:2530px" width="576" height="664" viewBox="0 0 576 664" role="img" aria-label="Photo of a business owner working through paperwork">
  <defs><linearGradient id="companyPhoto" x1="0" y1="0" x2="1" y2="1"><stop offset="0" stop-color="#7a5a42"/><stop offset=".5" stop-color="#c7a98c"/><stop offset="1" stop-color="#e8e2da"/></linearGradient></defs>
  <path fill="url(#companyPhoto)" d="M0 70C80 20 180-10 280 10C380 30 480 110 540 220C590 320 580 420 520 500C450 590 330 650 200 662C120 668 50 650 0 630Z"/>
</svg>
<div class="abs company">
  <h2>About Company</h2>
  <p>Harbourline Business Coach is here to help, support and turn your small business around, It may not be easy, it may not be pretty, it may not be conventional or what you want to hear but my only goal is to help you succeed in your small business struggling in Australia.</p>
  <p>I offer a 12 week fully supported and personally applied program, each week you complete the activities and we meet over Clearline Call where your actions are accountable and measurable.</p>
  <p>Every business and small business owner are different, so not one solution fits all, and that's exactly why I can make it personal for those who want to change and need it to happen now.</p>
</div>
<div class="abs company-actions"><div class="btn" style="width:186px">Read More</div><div class="btn btn-outline" style="width:210px">Free Download</div></div>

<!-- how it works -->
<div class="abs works">
  <h2>How It All Works</h2>
  <p>With your permission I breakdown your business, Staff, Products / Services, Marketing and Sales.</p>
  <p>Under each of these four key components are up to 30 or more components including your staff training and experience, business financials, public exposure and engagement with target market, current marketing and processes required to make income.</p>
  <div class="btn" style="width:198px;margin-top:30px">Get Started</div>
</div>
<div class="abs" style="left:608px;top:3317px;width:478px;height:346px;background:linear-gradient(135deg,#b9b3ad,#e6e1da 50%,#8b8a93);box-shadow:0 6px 16px rgba(0,0,0,.15)" role="img" aria-label="Photo of a team gathered in a bright office"></div>

<!-- activates -->
<p class="abs bridge">Regardless if you're a Harbourline Business Coach Free, Special Offer or Just a Bit More, Small Business Owner you allget one on one direct access to me each week along with mountains of accountable activities to turn your small business around into the dream you had hoped it could be.</p>
<div class="abs activates">
  <h2>Activates Include</h2>
  <ul>
    <li><svg class="ring" viewBox="0 0 20 20"><circle cx="10" cy="10" r="8.5" fill="none" stroke="var(--navy)" stroke-width="1.4"/><path d="M8.5 6.5L12 10L8.5 13.5" fill="none" stroke="var(--navy)" stroke-width="1.4"/></svg>Getting a measurable base line of the financials and existing marketing.</li>
    <li><svg class="ring" viewBox="0 0 20 20"><circle cx="10" cy="10" r="8.5" fill="none" stroke="var(--navy)" stroke-width="1.4"/><path d="M8.5 6.5L12 10L8.5 13.5" fill="none" stroke="var(--navy)" stroke-width="1.4"/></svg>Discussing the past ups and downs and looking forward to the future</li>
    <li><svg class="ring" viewBox="0 0 20 20"><circle cx="10" cy="10" r="8.5" fill="none" stroke="var(--navy)" stroke-width="1.4"/><path d="M8.5 6.5L12 10L8.5 13.5" fill="none" stroke="var(--navy)" stroke-width="1.4"/></svg>Understanding your product or service and how it fits into the current marketplace.</li>
    <li><svg class="ring" viewBox="0 0 20 20"><circle cx="10" cy="10" r="8.5" fill="none" stroke="var(--navy)" stroke-width="1.4"/><path d="M8.5 6.5L12 10L8.5 13.5" fill="none" stroke="var(--navy)" stroke-width="1.4"/></svg>Looking into the staff for potential opportunities or training.</li>
    <li><svg class="ring" viewBox="0 0 20 20"><circle cx="10" cy="10" r="8.5" fill="none" stroke="var(--navy)" stroke-width="1.4"/><path d="M8.5 6.5L12 10L8.5 13.5" fill="none" stroke="var(--navy)" stroke-width="1.4"/></svg>Understanding market trends and embracing a SWOT analysis</li>
    <li><svg class="ring" viewBox="0 0 20 20"><circle cx="10" cy="10" r="8.5" fill="none" stroke="var(--navy)" stroke-width="1.4"/><path d="M8.5 6.5L12 10L8.5 13.5" fill="none" stroke="var(--navy)" stroke-width="1.4"/></svg>Looking to establish a mastermind local group with a successful business</li>
    <li><svg class="ring" viewBox="0 0 20 20"><circle cx="10" cy="10" r="8.5" fill="none" stroke="var(--navy)" stroke-width="1.4"/><path d="M8.5 6.5L12 10L8.5 13.5" fill="none" stroke="var(--navy)" stroke-width="1.4"/></svg>Partnership opportunities</li>
    <li><svg class="ring" viewBox="0 0 20 20"><circle cx="10" cy="10" r="8.5" fill="none" stroke="var(--navy)" stroke-width="1.4"/><path d="M8.5 6.5L12 10L8.5 13.5" fill="none" stroke="var(--navy)" stroke-width="1.4"/></svg>Creating and applying marketing objectives</li>
    <li><svg class="ring" viewBox="0 0 20 20"><circle cx="10" cy="10" r="8.5" fill="none" stroke="var(--navy)" stroke-width="1.4"/><path d="M8.5 6.5L12 10L8.5 13.5" fill="none" stroke="var(--navy)" stroke-width="1.4"/></svg>How to give more to grow</li>
    <li><svg class="ring" viewBox="0 0 20 20"><circle cx="10" cy="10" r="8.5" fill="none" stroke="var(--navy)" stroke-width="1.4"/><path d="M8.5 6.5L12 10L8.5 13.5" fill="none" stroke="var(--navy)" stroke-width="1.4"/></svg>External learning materials applied as per needs such as specific podcast episodes or suggested books that relate to a special need to be supported</li>
  </ul>
</div>
<div class="abs free-link">10 Things you can start today in your small business to get you going again!</div>

<!-- newsletter & application -->
<div class="abs newsletter">
  <h2>Subscribe Our Newsletter</h2>
  <div class="field">Name</div>
  <div class="field">Email</div>
  <div class="submit">Submit</div>
</div>
<div class="abs application">
  <h2>Application</h2>
  <p>Placements are strictly limited to 28 per quarter as they are all managed personally for the best possible outcomes.</p>
  <p>You must have internet access, put the time aside between 1-2 hours a week on Clearline Call and be open to change and motivated and accountable to succeed with every scheduled meeting.</p>
  <div class="btn" style="width:198px;margin-top:12px">Get Started</div>
</div>

<!-- footer -->
<footer class="abs footer">
  <div class="social"><span></span><span></span><span></span><span></span></div>
  <div class="copyright">© 2018 Copyrights | All Rights Reserved</div>
</footer>

</body>
</html>
```